Brochure/flyer for our trip to Paris

Our company is taking us all on a summer trip to Paris. We have some key information that we need to tell everybody about the trip. We think a nicely designed brochure or flyer, which uses our brand colours and guidelines, would be something nice to keep during the trip and as a memento afterwards.

We are looking for a brochure or a flyer which contains all the info in the attached document.

This needs to happen really fast as we actually go to Paris on the 13th August. We also need time to print it!

We can provide a library of icons. All images in the document can be changed. you don't have to use the images in the document.

Target Market(s)

People in our company. They are fun and as this is for a party the flyer needs to feel uplifting.

Industry/Entity Type

Health

Font styles to use
Other font styles liked:
• Nexa - please see attached font.

Requirements
Must have
• Designers must stick to our brand guideline, font and the colours we use.
• Please also see attached content for the flyer.
• This website shows our style - https://www.lorventi.com/fr
Should not have
• Please don't make it too tacky or too much about French things. It can be a bit playful but not too much.

```html
<!DOCTYPE html>
<html lang="en">
<head>
<meta charset="utf-8">
<title>Paris Trip Brochure – Inside</title>
<link rel="stylesheet" href="https://fonts.googleapis.com/css2?family=Montserrat:wght@300;400;600;700;800&display=swap">
<style>
  :root {
    --accent-blue: #1c9fe0;
    --ink: #333333;
    --ink-soft: #666666;
    --paper: #ffffff;
    --backdrop: #e6e6e6;
    --fold: rgba(0,0,0,0.07);
    --sky-top: #f5f6f7;
    --sky-mid: #d8dadd;
    --city-low: #9a948b;
    --stone: #6e665e;
  }
  * { box-sizing: border-box; margin: 0; padding: 0; }
  html, body { width: 1200px; height: 1000px; overflow: hidden; }
  body {
    background: var(--backdrop);
    font-family: "Montserrat", sans-serif;
    color: var(--ink);
    position: relative;
  }
  .brochure {
    position: absolute; left: 50px; top: 75px;
    width: 1100px; height: 850px;
    background: var(--paper);
    box-shadow: 0 10px 30px rgba(0,0,0,0.18);
    display: flex; overflow: hidden;
  }
  .skyline-photo {
    position: absolute; left: 0; right: 0; bottom: 0; height: 300px;
    background: linear-gradient(to bottom, rgba(255,255,255,1) 0%, var(--sky-top) 30%, var(--sky-mid) 65%, var(--city-low) 100%);
  }
  .gargoyle-photo {
    position: absolute; left: 170px; bottom: 0; width: 220px; height: 250px;
    background: linear-gradient(to bottom, rgba(110,102,94,0.15) 0%, var(--stone) 35%, #4f4841 100%);
    border-radius: 110px 110px 0 0;
  }
  .panel {
    position: relative; width: 366.67px; height: 100%;
    padding: 44px 32px 0 34px;
    border-right: 1px solid var(--fold);
    z-index: 1;
  }
  .panel:last-child { border-right: none; }
  .heading { line-height: 1.05; margin-bottom: 16px; }
  .heading .lead {
    color: var(--accent-blue); font-weight: 800; font-size: 27px;
    text-transform: uppercase; letter-spacing: 0.5px;
  }
  .heading .rest {
    font-weight: 300; font-size: 27px; text-transform: uppercase; letter-spacing: 0.5px;
  }
  .heading.stacked .lead, .heading.stacked .rest { display: block; }
  .heading.compact .rest { font-size: 23.5px; letter-spacing: 0; white-space: nowrap; }
  .body-text { font-size: 14.5px; line-height: 1.42; color: var(--ink-soft); margin-bottom: 6px; }
  .body-text.justified { text-align: justify; }
  .tips { margin-top: 28px; }
  .tips .link { margin-top: 12px; word-break: break-all; }
  .day { font-weight: 700; font-size: 15px; color: var(--ink); margin: 14px 0 6px; }
  .day:first-of-type { margin-top: 0; }
  .indent { padding-left: 18px; }
  .emergency { margin-top: 30px; }
  .contacts { list-style: none; font-size: 17px; font-weight: 400; color: var(--ink); }
  .contacts li { display: flex; margin-bottom: 4px; }
  .contacts .name { width: 90px; }
  .contacts .phone { letter-spacing: 1px; }
  .phrase-intro { font-weight: 700; font-size: 14.5px; margin-bottom: 10px; }
  .phrases { list-style: none; font-size: 13.5px; line-height: 1.35; color: var(--ink-soft); }
  .phrases li { margin-bottom: 5px; }
  .phrases b { color: var(--ink); font-weight: 700; }
</style>
</head>
<body>
  <main class="brochure">
    <div class="skyline-photo" role="img" aria-label="Photograph of the Paris rooftops and skyline with the Eiffel Tower under a pale sky"></div>
    <div class="gargoyle-photo" role="img" aria-label="Photograph of a stone gargoyle statue overlooking Paris"></div>

    <section class="panel panel-metro">
      <h2 class="heading stacked"><span class="lead">How to</span><span class="rest">use the metro:</span></h2>
      <p class="body-text justified">You have each been given 3 Metro tickets to help you on your way. Although you may need additional tickets depending on what your plans are in your free time.</p>
      <p class="body-text justified">They are €4 for a single journey. Once you're in the Metro station, how to use the tickets is pretty self explanatory.</p>
      <p class="body-text justified">Tip from Marisol: the tickets have a magnetic strip so try and keep them away from bank cards etc. If you find that any of your tickets do not work, you can ask at the kiosk for a replacement.</p>
      <div class="tips">
        <h2 class="heading"><span class="lead">Top</span> <span class="rest">tips:</span></h2>
        <p class="body-text">The best way to find your way around is to use RouteBee or alternatively:</p>
        <p class="body-text link">http://www.transitpassage.fr/itineraires/en/tp/rechercheavancee</p>
      </div>
    </section>

    <section class="panel panel-itinerary">
      <h2 class="heading"><span class="lead">Itinerary</span></h2>
      <p class="day">13th August</p>
      <p class="body-text indent">Arrive in Paris at 11:17am local time. Drop bags to hotel, grab lunch and enjoy our 1 hour River Seine Tour.</p>
      <p class="day">Free time2:</p>
      <p class="body-text indent">3:07pm (you will need to go and officially check in at the hotel and get ready for the evening within this time)<br>7pm: Drinks and dinner at......<br>Late night drinks at........</p>
      <p class="day">The next day.....</p>
      <p class="body-text indent">Check out between 9:10am at the latest and enjoy some breakfast at the hotel. Casual walk up to Gare du nord, enjoying Paris that little bit more before we leave. Everyone must be at Gare du nord by 2pm at the very latest to check in!</p>
      <div class="emergency">
        <h2 class="heading stacked compact"><span class="lead">Emergency</span><span class="rest">internal contacts:</span></h2>
        <ul class="contacts">
          <li><span class="name">Maren</span><span class="phone">07700900143</span></li>
          <li><span class="name">Tobias</span><span class="phone">07700900278</span></li>
          <li><span class="name">Rupert</span><span class="phone">07700900391</span></li>
          <li><span class="name">Ilona</span><span class="phone">07700900456</span></li>
        </ul>
      </div>
    </section>

    <section class="panel panel-phrases">
      <h2 class="heading"><span class="lead">Some</span> <span class="rest">mustknow</span></h2>
      <p class="phrase-intro">French Phrases for Savvy Travellers:</p>
      <ol class="phrases">
        <li><b>1. Bonjour.</b> (Hello)</li>
        <li><b>2. Oui / Non</b> (Yes / No)</li>
        <li><b>3. Parlezvous anglais?</b> (Do you speak English?)</li>
        <li><b>4. Où est le métro?</b> (Where is the Metro?)</li>
        <li><b>5. Où est...?</b> (Where is...?)</li>
        <li><b>6. Où est le guichet ?</b> (Where is the ticket window?)</li>
        <li><b>7. Combien ça coûte?</b> (How much does it cost?)</li>
        <li><b>8. Merci!</b> (Thank you!)</li>
        <li><b>9. Bonsoir</b> (Hello/good evening)</li>
        <li><b>10. Au Revoir</b> (Goodbye)</li>
        <li><b>11. Puisje me connecter à Internet?</b> (Can I get on the internet?)</li>
        <li><b>12. Je ne comprends pas.</b> (I don't understand)</li>
        <li><b>13. Je ne sais pas.</b> (I don't know)</li>
        <li><b>14. Estce que vous pouvez l'écrire?</b> (Could you please write it down?)</li>
        <li><b>15. Pouvezvous m'aider, s'il vous plaît?</b> (Can you help me please?)</li>
      </ol>
    </section>
  </main>
</body>
</html>
```